Quorva - corporate Business Card

We need a good look and innovative business card for a new start up company based in Los Angeles called "Quorva". We are in a payment business, including payment card, app, and ewallet. We are expert in online payment and Card not present (CNP) transaction.
We need an innovative, modern business card.

Our logo font is Aero Matics

Target Market(s)

Startup - Bank - Online Payment - Card Manufacturing

Industry/Entity Type

Startup

Contact Information for Business Card

phone: 555 014 7396 - Address: 4172 Marlowe blvd, Fenwick Park, OR 97204

Requirements
Must have
• Message: innovative, professional, expert, high tech, trust, online payment expert, security
Nice to have
• no comment
Should not have
• no Comment

```html
<!DOCTYPE html>
<html lang="en">
<head>
<meta charset="utf-8">
<title>Quorva – Business Card</title>
<link href="https://fonts.googleapis.com/css2?family=Open+Sans:wght@400;600;700&display=swap" rel="stylesheet">
<style>
  :root {
    --brand-red: #b8202f;
    --stage: #1c1c1c;
    --card-white: #ffffff;
    --tint: #f8ece7;
    --ink-grey: #666666;
  }
  * { margin: 0; padding: 0; box-sizing: border-box; }
  html, body { width: 1200px; height: 741px; overflow: hidden; }
  body {
    background: var(--stage);
    font-family: "Open Sans", Arial, sans-serif;
    position: relative;
  }
  .card {
    position: absolute;
    top: 229px;
    width: 494px;
    height: 282px;
    border-radius: 12px;
    overflow: hidden;
  }
  .card-front { left: 100px; background: var(--brand-red); }
  .card-back { left: 606px; background: var(--card-white); }

  .brand { position: absolute; display: flex; align-items: center; }
  .brand-dot { border-radius: 50%; flex: none; }
  .brand-name { font-weight: 600; line-height: 1; letter-spacing: 1px; }

  .card-front .brand { left: 108px; top: 99px; }
  .card-front .brand-dot { width: 84px; height: 84px; background: var(--card-white); margin-right: 12px; }
  .card-front .brand-name { font-size: 58px; color: var(--card-white); margin-top: -8px; }

  .card-back .brand { left: 25px; top: 27px; }
  .card-back .brand-dot { width: 74px; height: 74px; background: var(--brand-red); margin-right: 10px; }
  .card-back .brand-name { font-size: 48px; color: var(--brand-red); margin-top: -8px; }

  .tint-circle {
    position: absolute;
    left: 296px; top: -19px;
    width: 320px; height: 320px;
    border-radius: 50%;
    background: var(--tint);
  }
  .holder { position: absolute; left: 25px; top: 131px; }
  .holder-name { font-size: 18px; font-weight: 700; color: var(--brand-red); line-height: 1.1; }
  .holder-role { font-size: 14px; color: var(--ink-grey); line-height: 1.1; }

  .address { position: absolute; left: 26px; top: 184px; font-size: 13.5px; line-height: 16px; color: var(--ink-grey); }
  .contact { position: absolute; left: 25px; top: 225px; font-size: 13.5px; color: var(--ink-grey); }
  .contact-line { display: flex; align-items: center; height: 18px; }
  .contact-line svg { width: 15px; height: 15px; margin-right: 4px; flex: none; }
</style>
</head>
<body>
  <section class="card card-front" aria-label="Card front">
    <div class="brand">
      <span class="brand-dot"></span>
      <span class="brand-name">quorva</span>
    </div>
  </section>

  <section class="card card-back" aria-label="Card back">
    <div class="tint-circle"></div>
    <div class="brand">
      <span class="brand-dot"></span>
      <span class="brand-name">quorva</span>
    </div>
    <div class="holder">
      <p class="holder-name">Daniel Reyes</p>
      <p class="holder-role">Managing Director</p>
    </div>
    <p class="address">4172 Marlowe blvd,<br>Fenwick Park, OR 97204</p>
    <div class="contact">
      <p class="contact-line">
        <svg viewBox="0 0 16 16" aria-hidden="true"><circle cx="8" cy="8" r="8" fill="var(--brand-red)"/><path d="M4 6.2c0-1 1.8-1.7 4-1.7s4 .7 4 1.7v.6h-2v-.7H6v.7H4z M5 8h6l.8 3.5H4.2z" fill="#fff"/></svg>
        555 014 7396
      </p>
      <p class="contact-line">
        <svg viewBox="0 0 16 16" aria-hidden="true"><circle cx="8" cy="8" r="8" fill="var(--brand-red)"/><rect x="4" y="5" width="8" height="6" fill="#fff"/><path d="M4 5l4 3.3L12 5" fill="none" stroke="var(--brand-red)" stroke-width="1"/></svg>
        hello@quorvapay.com
      </p>
    </div>
  </section>
</body>
</html>
```